Create a proposal + product powerpoint

Please see the powerpoint for the slides. There are about 20 slides to be created. Rest of them are for reference and show the design that I like.

I would like to move fast on this, since I need to present it next week (in the week of April 21st).

Please download the current content from here:
https://www.parcelbrook.net/fetch/qRtVmXzLwPkNbYcD

Please make at least 4 slides with the specific content so I can assess your design style.

Target Market(s)

Business Audience and very senior technical audience
Decision Makers

Industry/Entity Type

Product

Colors
e34297
a64599

Requirements
Must have
• Should be very clean, crisp.

I like to use Icons as shown in the powerpoint.... Please see the appendix of the slide deck that shows the various icons. Most of them just have plain text, and I would like to organize so that it does not look like some is just reading text.

I would like to focus on the design aspects so that the audience is clear on how the solution works.

Every page should some graphic element based on the slides shown in the appendix.

```html
<!DOCTYPE html>
<html lang="en">
<head>
<meta charset="utf-8">
<title>Lifecycle Management Solution</title>
<link href="https://fonts.googleapis.com/css2?family=Magra:wght@400;700&family=Saira:wght@400&display=swap" rel="stylesheet">
<style>
  :root {
    --pink: #e34297;
    --purple: #a64599;
    --tile: #0099dd;
    --text: #2b2b2b;
    --white: #ffffff;
    --wash: #f6eef6;
  }
  html, body { margin: 0; padding: 0; overflow: hidden; background: var(--white); }
  .slide {
    position: relative;
    width: 1200px;
    height: 900px;
    overflow: hidden;
    background: var(--white);
    font-family: "Saira", sans-serif;
  }
  .backdrop-wave {
    position: absolute;
    left: 0; top: 180px;
    width: 1200px; height: 642px;
    background:
      radial-gradient(ellipse 70% 30% at 40% 85%, rgba(166,69,153,0.18), transparent 70%),
      radial-gradient(ellipse 60% 40% at 20% 60%, rgba(227,66,151,0.08), transparent 70%),
      linear-gradient(180deg, rgba(246,238,246,0) 0%, var(--wash) 70%, rgba(246,238,246,0.6) 100%);
  }
  .title-accent {
    position: absolute;
    left: 0; top: 30px;
    width: 15px; height: 67px;
    background: var(--purple);
  }
  .slide-title {
    position: absolute;
    left: 28px; top: 28px;
    margin: 0;
    font-family: "Magra", sans-serif;
    font-weight: 400;
    font-size: 52px;
    color: var(--pink);
    letter-spacing: 1px;
  }
  .brand-name {
    position: absolute;
    right: 44px; top: 48px;
    font-family: "Magra", sans-serif;
    font-weight: 700;
    font-size: 38px;
    color: var(--purple);
  }
  .content-heading {
    position: absolute;
    left: 32px; top: 182px;
    margin: 0;
    font-family: "Magra", sans-serif;
    font-weight: 700;
    font-size: 38px;
    color: var(--purple);
  }
  .content-body {
    position: absolute;
    left: 32px; top: 240px;
    width: 602px;
  }
  .content-body p {
    margin: 0 0 36px;
    font-size: 22px;
    line-height: 36px;
    color: var(--text);
    text-align: justify;
    text-align-last: left;
  }
  .icon-grid {
    position: absolute;
    left: 680px; top: 256px;
    display: grid;
    grid-template-columns: 234px 234px;
    grid-template-rows: 234px 234px;
    gap: 13px;
  }
  .icon-tile {
    background: var(--tile);
    display: flex;
    align-items: center;
    justify-content: center;
  }
  .icon-tile svg { width: 150px; height: 150px; }
  .footer-band {
    position: absolute;
    left: 0; bottom: 0;
    width: 1200px; height: 78px;
    background: var(--pink);
    border-top: 4px solid var(--purple);
  }
  .copyright {
    position: absolute;
    right: 18px; bottom: 20px;
    font-family: "Magra", sans-serif;
    font-size: 22px;
    color: var(--white);
  }
</style>
</head>
<body>
<div class="slide">
  <div class="backdrop-wave" role="img" aria-label="Soft flowing purple line waves in the background"></div>

  <div class="title-accent"></div>
  <h1 class="slide-title">Lifecycle Management Solution</h1>
  <div class="brand-name">LOGO HERE</div>

  <h2 class="content-heading">Lorem ipsum dolor sit ipsum</h2>
  <div class="content-body">
    <p>Lorem ipsum dolor sit ipsum Lorem ipsum dolor sit ipsum Lorem ipsum dolor sit ipsum Lorem ipsum dolor sit ipsum lorem ipsum dolor sit ipsum Lorem ipsum dolor sit ipsum Lorem ipsum dolor sit ipsum</p>
    <p>Lorem ipsum dolor sit ipsum Lorem ipsum dolor sit ipsum Lorem ipsum dolor sit ipsum Lorem ipsum dolor sit ipsum lorem ipsum dolor sit ipsum Lorem ipsum dolor sit ipsum Lorem ipsum dolor sit ipsum Lorem ipsum dolor sit ipsum</p>
    <p>Lorem ipsum dolor sit ipsum Lorem ipsum dolor sit ipsum Lorem ipsum dolor sit ipsum Lorem ipsum dolor sit ipsum lorem ipsum dolor sit</p>
  </div>

  <div class="icon-grid">
    <div class="icon-tile">
      <svg viewBox="0 0 100 100" aria-label="Presentation board icon" role="img">
        <rect x="46" y="8" width="8" height="7" rx="2" fill="#fff"/>
        <rect x="6" y="15" width="88" height="7" rx="2" fill="#fff"/>
        <rect x="12" y="22" width="76" height="50" fill="none" stroke="#fff" stroke-width="6"/>
        <path d="M38 76 L26 92 M50 76 L50 90 M62 76 L74 92" stroke="#fff" stroke-width="6" stroke-linecap="round"/>
      </svg>
    </div>
    <div class="icon-tile">
      <svg viewBox="0 0 100 100" aria-label="Set square icon" role="img">
        <path d="M94 4 L94 92 L6 92 Z M80 36 L80 78 L38 78 Z" fill="#fff" fill-rule="evenodd"/>
        <g stroke="var(--tile)" stroke-width="2">
          <path d="M94 20 H88 M94 32 H90 M94 44 H88 M94 56 H90 M94 68 H88 M94 80 H90"/>
          <path d="M20 92 V86 M32 92 V88 M44 92 V86 M56 92 V88 M68 92 V86 M80 92 V88"/>
        </g>
      </svg>
    </div>
    <div class="icon-tile">
      <svg viewBox="0 0 100 100" aria-label="Puzzle piece icon" role="img">
        <path fill="#fff" d="M30 38 H48 C44 30 42 24 48 18 C54 12 66 14 68 22 C70 28 66 32 64 38 H82 V56 C74 52 68 52 64 58 C60 64 62 74 70 76 C76 78 80 76 82 74 V92 H30 V74 C24 78 14 78 10 70 C6 62 12 52 20 52 C24 52 28 54 30 56 Z"/>
      </svg>
    </div>
    <div class="icon-tile">
      <svg viewBox="0 0 100 100" aria-label="Compass icon" role="img">
        <circle cx="50" cy="50" r="42" fill="none" stroke="#fff" stroke-width="8"/>
        <path d="M70 22 L54 54 L46 46 Z" fill="#fff"/>
        <path d="M30 78 L46 46 L54 54 Z" fill="#fff"/>
        <circle cx="50" cy="50" r="4" fill="var(--tile)"/>
      </svg>
    </div>
  </div>

  <div class="footer-band"></div>
  <div class="copyright">Copyright text here</div>
</div>
</body>
</html>
```